Varnick Fundraising E-mail Campaign

I intend to use Constant Contact to send donors 4 separate e-mail messages with pictures, text and a hot link, “Give to Restore Marlowe.” E-mails will spaced about 3 days apart. I would like the first e-mail to go out on Monday, December 17. The e-mail campaign is part of a board match annual appeal fundraising campaign for a not for profit sleep away Christian camp. Our hope is to raise $40,000.00+

Target Market(s)

Members in Constant Contact list

Colors

Designer to choose colors to be used in the design.

Requirements
Must have
• E- mail recipient must be able to access hot link

```html
<!DOCTYPE html>
<html lang="en">
<head>
<meta charset="utf-8">
<title>Varnick Camp – Restore Marlowe Lake</title>
<link href="https://fonts.googleapis.com/css2?family=Roboto:wght@400;700&display=swap" rel="stylesheet">
<style>
  :root {
    --page-bg: #adcb88;
    --sheet: #ffffff;
    --alert-red: #e01f2b;
    --ink-green: #0b7a3e;
    --frame-green: #a9cb84;
    --hill-green: #17a64a;
    --lake-blue: #22b0dc;
    --photo-shade: #2f4a22;
    --photo-light: #7c9a5e;
  }
  * { box-sizing: border-box; margin: 0; padding: 0; }
  html, body { width: 1200px; height: 1155px; overflow: hidden; }
  body {
    background: var(--page-bg);
    font-family: "Roboto", Arial, sans-serif;
    color: var(--ink-green);
    position: relative;
  }
  .email {
    position: absolute; left: 376px; top: 0;
    width: 448px; height: 1155px;
    background: var(--sheet);
    overflow: hidden;
  }
  .donate-bar {
    height: 24px; background: var(--alert-red);
    text-align: center; line-height: 24px;
  }
  .donate-bar a {
    color: #fff; font-weight: 700; font-size: 15px; text-decoration: underline;
  }
  .brand {
    position: absolute; top: 34px; left: 0; width: 100%;
    display: flex; justify-content: center; align-items: center; gap: 8px;
  }
  .brand-mark { width: 18px; height: 18px; background: var(--hill-green); }
  .brand-name { font-size: 18px; font-weight: 400; color: var(--ink-green); letter-spacing: 1px; }
  .photo {
    position: absolute; left: 24px; width: 400px; height: 264px;
    border: 5px solid var(--frame-green);
    background: radial-gradient(ellipse at 70% 30%, var(--photo-light), var(--photo-shade) 75%);
  }
  .photo-one { top: 77px; }
  .photo-two { top: 470px; }
  .story {
    position: absolute; top: 365px; left: 18px; width: 412px;
    text-align: center; font-size: 11.2px; line-height: 16px;
  }
  .copy { position: absolute; left: 8px; width: 420px; font-size: 11.2px; line-height: 16px; }
  .copy-intro { top: 750px; }
  .copy-close { top: 913px; }
  .gift-list {
    position: absolute; top: 807px; left: 43px;
    font-size: 11.2px; line-height: 16px; list-style: circle;
  }
  .gift-list li { padding-left: 2px; }
  .gift-list li::marker { font-size: 9px; }
  .cta {
    position: absolute; top: 954px; left: 0; width: 100%;
    text-align: center; font-size: 14.5px; line-height: 17px;
  }
  .cta a { color: var(--ink-green); }
  .contact {
    position: absolute; top: 1013px; left: 8px;
    font-size: 9px; line-height: 13px; font-style: normal;
  }
  .landscape {
    position: absolute; left: 0; bottom: 0;
    width: 448px; height: 82px;
    background: linear-gradient(to bottom, var(--hill-green) 0%, var(--hill-green) 58%, var(--lake-blue) 100%);
  }
</style>
</head>
<body>
  <main class="email">
    <div class="donate-bar"><a href="http://varnickcamp.org/support">DONATE NOW</a></div>

    <div class="brand">
      <span class="brand-mark"></span>
      <span class="brand-name">VARNICK</span>
    </div>

    <div class="photo photo-one" role="img" aria-label="Three children crouching at the edge of a stream with nets among green leaves"></div>

    <p class="story">A revitalized Marlowe Lake can do so much for children like Nora. Research shows that playing outdoors will (1) enhance Nora’s ability to learn, (2) stimulates Nora’s creativity, (3) increases Nora’s sense of well-being and (4) improve Nora’s social skills.&nbsp; Research also shows that youth who attend Christian summer camp grow to interpret all of life through a lens of faith.</p>

    <div class="photo photo-two" role="img" aria-label="Children exploring a creek bank at camp"></div>

    <p class="copy copy-intro">You can help us provide Nora and children like her by taking advantage of the Revitalize Camp Marlowe Lake Matching Challenge</p>

    <ul class="gift-list">
      <li>$100.00 will buy: material for a picnic table</li>
      <li>$250.00 will buy: materials to improve the tent frames</li>
      <li>$500.00 will buy: materials to repair the bath house roof</li>
      <li>$1,000.00 will buy: a new tent to replace one damaged by tornado</li>
      <li>$5,000.00 will buy: half the roofing material for Marlowe Dining Hall</li>
    </ul>

    <p class="copy copy-close">If you haven’t done so, please donate today.</p>

    <p class="cta"><a href="http://varnickcamp.org/support">Visit http://varnickcamp.org/support and click on<br>"Restore Marlowe</a></p>

    <address class="contact">
      Contact:<br>
      48 Marlowe Lake Road Varnick, NY 10990<br>
      Phone: 555-014-2290 Fax: 555-014-2291<br>
      E-Mail: hello@varnickcamp.org
    </address>

    <div class="landscape" role="img" aria-label="Illustrated green hills beside a blue lake with a leafy tree"></div>
  </main>
</body>
</html>
```